Website for Dental Office - The Bright Arch Clinic

The bright arch clinic is a dental office offering cosmetic dentistry, general dentistry, and multi-specialty dental care all under one roof in our state-of-the-art cosmetic dental center. We are particularly striving to provide services that fit the need of the young generation. Thus, we hope to have a modern, professional concise website that represents our spirit.

*Should be able to switch from English to Chinese

6 sections besides homepage:
Home, Meet us, Services,
Patient Info, Cases&Reviews, Blog, Contact

The Services sections should contain multiple subsections such as cleaning and prevention, cosmetic dentistry, implant dentistry, removable dentures, etc...
The Patient Info section is also intended to contain several subsections such as
New Patient offer, accepted Insurance, patient portal, helpful tips, etc...

Target Market(s)

young generation

Coding

Coded - Design and coding required

Number of Pages Required

5+ page

Font styles to use
Sans Serif

Colors
0592cd
33a6d7
85cae6
00a990
33b8a4
86cfc6
cee9f5
cfeae6
3277b5

Requirements
Must have
• *Should be able to switch from English to Chinese
Nice to have
• http://www.thebrightarchclinic.com/
• As a reference, the above link is the current website, but we would like to change the appearance and the content (our new logo's picture is attached)

```html
<!DOCTYPE html>
<html lang="en">
<head>
<meta charset="utf-8">
<title>Blog – The Bright Arch Clinic</title>
<link href="https://fonts.googleapis.com/css2?family=Montserrat:wght@400;500;600;700;800&display=swap" rel="stylesheet">
<style>
:root{
  --blue:#0592cd; --blue2:#33a6d7; --sky:#85cae6; --navy:#3277b5;
  --teal:#00a990; --teal2:#33b8a4; --ice:#cee9f5; --mist:#dff2fb;
  --ink:#111; --body:#666; --card:#f4f4f4; --foot:#f1f1f1; --bar:#e8e8e8;
}
*{margin:0;padding:0;box-sizing:border-box}
html,body{width:853px;height:1200px;overflow:hidden;background:#fff}
body{font-family:"Montserrat",sans-serif;color:var(--body);position:relative}
.abs{position:absolute}
.topline{left:0;top:0;width:853px;height:2px;background:var(--navy)}
.hero-bg{left:0;top:0;width:853px;height:420px;background:linear-gradient(#d6f0fc 40%,#fff 100%)}
.curve{left:0;top:0}
.brand{left:115px;top:14px;width:155px;display:flex;align-items:center;gap:8px;font-size:14px;line-height:16px;font-weight:700;color:var(--blue2)}
.brand i{flex:none;width:28px;height:28px;background:var(--blue2);border-radius:3px}
.nav{left:283px;top:28px;display:flex;gap:13px;font-size:7.4px;font-weight:500;color:#444;text-transform:uppercase}
.nav .on{color:var(--teal)}
.phone{left:615px;top:-12px;width:80px;height:80px;border-radius:50%;background:var(--navy);color:#fff;text-align:center;font-size:8.4px;font-weight:700;padding-top:25px}
.phone svg{display:block;margin:0 auto 5px}
.lang{left:703px;top:21px;width:35px;height:21px;background:var(--teal);border-radius:2px;color:#fff;font-size:7px;display:flex;align-items:center;justify-content:center;gap:3px}
.title{left:0;width:853px;top:152px;text-align:center;font-size:29px;font-weight:800;color:var(--ink);letter-spacing:.5px}
.lead{left:240px;width:373px;top:197px;text-align:center;font-size:7.6px;line-height:14px}
.card{background:var(--card)}
.post h2{font-size:8.8px;font-weight:700;color:var(--ink);line-height:14px}
.side h2{font-size:7.6px;font-weight:500;color:var(--ink);line-height:14px}
.date{font-size:7px;color:var(--navy);margin:4px 0 10px}
.post p{font-size:7.6px;line-height:13.9px;margin-bottom:14px}
.side p{font-size:7.6px;line-height:13.9px;margin-bottom:6px}
.more{font-size:7px;font-weight:600;color:var(--teal);text-transform:uppercase}
.footbg{left:0;top:939px;width:853px;height:261px;background:var(--foot)}
.cta{left:115px;top:880px}
.cta-small{left:130px;top:918px;font-size:8px;color:#fff}
.cta-big{left:130px;top:934px;font-size:24.5px;font-weight:700;color:#fff;letter-spacing:.3px}
.btn{left:557px;top:937px;width:159px;height:32px;border-radius:16px;background:#fff;color:#222;font-size:8.6px;font-weight:700;display:flex;align-items:center;justify-content:center}
.fbox{left:157px;top:1032px;width:48px;height:48px;background:var(--sky);border-radius:4px}
.fbrand{left:115px;width:138px;text-align:center;top:1089px;font-size:11.5px;font-weight:700;color:var(--blue2);white-space:nowrap}
.social{left:128px;top:1112px;display:flex;gap:6px}
.social i{width:24px;height:24px;border-radius:50%}
.fcol h3{font-size:8px;font-weight:700;color:#222;letter-spacing:.4px;margin-bottom:8px}
.fcol li{list-style:none;font-size:7.2px;line-height:13.3px}
.hours{border-collapse:collapse}
.hours td{font-size:7.2px;line-height:13.3px;padding:0 6px 0 0}
.hours td b{font-weight:700;color:#444}
.ci{font-size:7.2px;line-height:13.3px;display:flex;gap:8px;margin-bottom:9px}
.bar{left:0;top:1168px;width:853px;height:32px;background:var(--bar);font-size:7.4px;display:flex;justify-content:space-between;align-items:center;padding:0 115px}
.bar a{color:var(--navy);text-decoration:none}
.bar .r{color:var(--teal)}
</style>
</head>
<body>
<div class="abs hero-bg"></div>
<svg class="abs curve" width="853" height="110" viewBox="0 0 853 110"><path d="M0 0H853V48Q640 110 426 108Q213 110 0 48Z" fill="#fff"/></svg>
<div class="abs topline"></div>

<div class="abs brand"><i></i><span>The Bright Arch<br>Clinic</span></div>
<nav class="abs nav"><span>Home</span><span>Meet Us</span><span>Services</span><span>Patient Info</span><span>Reviews</span><span class="on">Blog</span><span>Contact</span></nav>
<div class="abs phone"><svg width="14" height="14" viewBox="0 0 24 24"><path fill="#fff" d="M6.6 10.8a15 15 0 0 0 6.6 6.6l2.2-2.2c.3-.3.7-.4 1-.2 1.1.4 2.3.6 3.6.6.6 0 1 .4 1 1V20c0 .6-.4 1-1 1A17 17 0 0 1 3 4c0-.6.4-1 1-1h3.5c.6 0 1 .4 1 1 0 1.3.2 2.5.6 3.6.1.3 0 .7-.2 1z"/></svg>555.014.2790</div>
<div class="abs lang">汉语 <svg width="6" height="4" viewBox="0 0 6 4"><path d="M0.5 0.5L3 3L5.5 0.5" stroke="#fff" fill="none"/></svg></div>

<h1 class="abs title">BLOG</h1>
<p class="abs lead">Lorem Ipsum is dummy text of the printing and typesetting industry. Lorem Ipsum has been the industry's standard dummy text.</p>

<div class="abs" role="img" aria-label="Close-up photo of a smiling woman with wavy hair" style="left:115px;top:250px;width:400px;height:267px;background:linear-gradient(120deg,#c8b394 0%,#6b4a33 35%,#2a2220 60%,#a27862 80%,#3a2c26 100%)"></div>
<article class="abs card post" style="left:115px;top:517px;width:400px;height:293px;padding:14px 13px">
  <h2>Lorem Ipsum is dummy text of the printing and typesetting industry.</h2>
  <div class="date">7 September 2019</div>
  <p>Lorem Ipsum is simply dummy text of the printing and typesetting industry. Lorem Ipsum has been the industry's standard dummy text ever since the 1500s, when an unknown printer took a galley of type and scrambled it to make a type specimen book.</p>
  <p>It has survived not only five centuries, but also the leap into electronic typesetting, remaining essentially unchanged. It was popularised in the 1960s with the release of Letraset sheets containing Lorem Ipsum passages, and more recently with desktop publishing software like Aldus PageMaker including versions of Lorem Ipsum.Lorem Ipsum is simply dummy text of the printing and typesetting industry. Lorem Ipsum has been the industry's standard dummy text ever since the 1500s, when an unknown printer took a galley of type and scrambled it to make a type specimen book.</p>
  <p>It has survived not only five centuries, but also the leap into electronic typesetting, remaining essentially unchanged. It was popularised in the 1960s with the release of Letraset sheets containing Lorem Ipsum passages, and more recently with desktop publishing software like Aldus PageMaker including versions of Lorem Ipsum.</p>
</article>

<div class="abs" role="img" aria-label="Photo of a bright dental treatment room with patient chair" style="left:547px;top:250px;width:191px;height:128px;background:linear-gradient(160deg,#f4f6f8 0%,#dfe4e8 55%,#9aa0a5 100%)"></div>
<article class="abs card side" style="left:547px;top:378px;width:191px;height:139px;padding:14px 8px">
  <h2>Lorem Ipsum is dummy text of the printing and typesetting industry.</h2>
  <div class="date">7 September 2019</div>
  <p>Lorem Ipsum is dummy text of the printing and typesetting industry. Lorem Ipsum has been the industry's standard dummy text.</p>
  <div class="more">Read More</div>
</article>

<div class="abs" role="img" aria-label="Photo of a dentist in a white coat examining an item in the clinic" style="left:547px;top:544px;width:191px;height:128px;background:linear-gradient(150deg,#5b5f61 0%,#b9bfc2 40%,#eef0f0 60%,#8b9093 100%)"></div>
<article class="abs card side" style="left:547px;top:672px;width:191px;height:138px;padding:14px 8px">
  <h2>Lorem Ipsum is dummy text of the printing and typesetting industry.</h2>
  <div class="date">7 September 2019</div>
  <p>Lorem Ipsum is dummy text of the printing and typesetting industry. Lorem Ipsum has been the industry's standard dummy text.</p>
  <div class="more">Read More</div>
</article>

<div class="abs footbg"></div>
<svg class="abs cta" width="623" height="118" viewBox="0 0 623 118">
  <defs><linearGradient id="ctaGrad" x1="0" x2="1"><stop offset="0" stop-color="#0592cd"/><stop offset="1" stop-color="#00a990"/></linearGradient></defs>
  <path d="M0 6Q0 0 6 0L617 31Q623 32 623 37V112Q623 118 617 118H6Q0 118 0 112Z" fill="url(#ctaGrad)"/>
</svg>
<div class="abs cta-small">Lorem Ipsum is dummy text of the printing and typesetting.</div>
<div class="abs cta-big">YOUR SMILE. OUR PASSION.</div>
<div class="abs btn">BOOK AN APPOINTMENT</div>

<div class="abs fbox"></div>
<div class="abs fbrand">The Bright Arch Clinic</div>
<div class="abs social"><i style="background:var(--blue2)"></i><i style="background:var(--navy)"></i><i style="background:var(--teal)"></i><i style="background:var(--teal2)"></i></div>

<div class="abs fcol" style="left:277px;top:1029px"><h3>USEFUL LINKS</h3><ul><li>Home</li><li>Meet Us</li><li>Services</li><li>Patient Info</li><li>Case &amp; Reviews</li><li>Blog</li><li>Contact</li></ul></div>
<div class="abs fcol" style="left:439px;top:1029px"><h3>OPENING HOURS</h3>
  <table class="hours"><tr><td>Sunday &amp; Monday</td><td><b>Closed</b></td></tr><tr><td>Tuesday</td><td><b>9:30AM – 5:00PM</b></td></tr><tr><td>Wednesday</td><td><b>Closed</b></td></tr><tr><td>Thursday</td><td><b>9:30AM – 5:00PM</b></td></tr><tr><td>Friday</td><td><b>9:00AM – 5:00PM</b></td></tr><tr><td>Saturday</td><td><b>9:00AM – 5:00PM</b></td></tr></table></div>
<div class="abs fcol" style="left:601px;top:1029px;width:140px"><h3>CONTACT INFO</h3>
  <div class="ci"><svg width="8" height="11" viewBox="0 0 8 11"><path d="M4 0a4 4 0 0 1 4 4c0 3-4 7-4 7S0 7 0 4a4 4 0 0 1 4-4z" fill="#00a990"/><circle cx="4" cy="4" r="1.5" fill="#fff"/></svg><span>270 Maple Avenue, Suite 12, Fairview MA 02199</span></div>
  <div class="ci" style="font-size:10px;align-items:center"><svg width="10" height="10" viewBox="0 0 24 24"><path fill="#3277b5" d="M6.6 10.8a15 15 0 0 0 6.6 6.6l2.2-2.2c.3-.3.7-.4 1-.2 1.1.4 2.3.6 3.6.6.6 0 1 .4 1 1V20c0 .6-.4 1-1 1A17 17 0 0 1 3 4c0-.6.4-1 1-1h3.5c.6 0 1 .4 1 1 0 1.3.2 2.5.6 3.6.1.3 0 .7-.2 1z"/></svg>555.014.2790</div>
  <div class="ci" style="align-items:center"><svg width="10" height="8" viewBox="0 0 10 8"><rect width="10" height="8" rx="1" fill="#33a6d7"/><path d="M0.5 1L5 4.5L9.5 1" stroke="#fff" fill="none"/></svg>hello@brightarchclinic.com</div>
</div>

<div class="abs bar"><span>© <a>The Bright Arch Clinic</a> – 2019. All Rights Reserved.</span><span class="r">Fairview Botox and Dermal Fillers</span></div>
</body>
</html>
```